- Redesign our business card
- Logo remains unchanged
- Current business card attached

Target Market(s)

We are a property management company

Industry/Entity Type

Business

```html
<!DOCTYPE html>
<html lang="en">
<head>
<meta charset="utf-8">
<title>Harlow Property Group – Business Card</title>
<link rel="stylesheet" href="https://fonts.googleapis.com/css2?family=Arimo:wght@400;700&display=swap">
<style>
  :root {
    --stage: #000000;
    --paper: #ffffff;
    --olive: #7f7d43;
    --sand: #e2d5b0;
    --slate: #6b6b6d;
    --ink: #3a3a3a;
    --muted: #5a5a5a;
  }
  * { margin: 0; padding: 0; box-sizing: border-box; }
  html, body {
    width: 1200px; height: 900px; overflow: hidden;
    background: var(--stage);
    font-family: "Arimo", Arial, sans-serif;
  }
  .canvas { position: relative; width: 1200px; height: 900px; }

  .card { position: absolute; top: 66px; width: 428px; height: 748px; overflow: hidden; }
  .card--front { left: 116px; background: var(--paper); }
  .card--back  { left: 592px; background: var(--olive); }

  .card__band { position: absolute; bottom: 0; left: 0; height: 24px; }
  .card--front .card__band { width: 280px; background: var(--olive); }
  .card--back  .card__band { width: 280px; background: var(--sand); }

  /* brand lockup, front */
  .brand { position: absolute; left: 94px; top: 94px; }
  .brand__mark { width: 40px; height: 40px; background: var(--olive); margin-bottom: 18px; }
  .brand__name { font-weight: 700; font-size: 15px; letter-spacing: 0.6px; color: var(--olive); text-transform: uppercase; }
  .brand__tagline { font-size: 11.5px; letter-spacing: 0.6px; color: var(--olive); text-transform: uppercase; margin-top: 2px; }

  /* contact block */
  .contact { position: absolute; left: 44px; top: 438px; }
  .contact__name { font-weight: 700; font-size: 16px; letter-spacing: 0.4px; color: var(--olive); text-transform: uppercase; }
  .contact__role { font-size: 15px; color: var(--muted); margin-top: 3px; }
  .contact__address { margin-top: 14px; font-weight: 700; font-size: 12.5px; line-height: 26px; color: var(--ink); text-transform: uppercase; }
  .contact__lines { margin-top: 10px; list-style: none; font-size: 12.5px; line-height: 27px; color: var(--muted); }

  /* back */
  .back-brand { position: absolute; left: 0; right: 0; top: 270px; text-align: center; }
  .back-brand__mark { width: 120px; height: 120px; margin: 0 auto 50px; background: var(--sand); }
  .back-brand__name { font-weight: 700; font-size: 22px; letter-spacing: 0.8px; color: var(--paper); text-transform: uppercase; }
  .back-brand__tagline { font-size: 15px; letter-spacing: 0.8px; color: var(--sand); text-transform: uppercase; margin-top: 4px; }
</style>
</head>
<body>
<main class="canvas">
  <section class="card card--front">
    <div class="brand">
      <div class="brand__mark"></div>
      <p class="brand__name">Harlow Property Group</p>
      <p class="brand__tagline">Strata Management Services</p>
    </div>

    <div class="contact">
      <p class="contact__name">Daniel Harlow</p>
      <p class="contact__role">Licensed Strata Manager</p>
      <p class="contact__address">
        PO Box 48, Elmwood NSW<br>
        2041 12/5-18 Linden Street Elm<br>
        Wood NSW 2041
      </p>
      <ul class="contact__lines">
        <li>T: 02 9555 0142</li>
        <li>F: 02 9555 0187</li>
        <li>M: 0412 555 309</li>
        <li>E: info@harlowproperty.com.au</li>
        <li>www.harlowproperty.com.au</li>
      </ul>
    </div>
    <div class="card__band"></div>
  </section>

  <section class="card card--back">
    <div class="back-brand">
      <div class="back-brand__mark"></div>
      <p class="back-brand__name">Harlow Property Group</p>
      <p class="back-brand__tagline">Strata Management Services</p>
    </div>
    <div class="card__band"></div>
  </section>
</main>
</body>
</html>
```